wealth management firm, professional group, new model

we have a logo that works but we need a card, white background using our colors...clean look

our tag line if can be used in

The Path from Saver to Steward

```html
<!DOCTYPE html>
<html lang="en">
<head>
<meta charset="UTF-8">
<title>Arvale Wealth Partners – Business Card</title>
<link href="https://fonts.googleapis.com/css2?family=Montserrat:wght@400;500&display=swap" rel="stylesheet">
<style>
  :root {
    --navy: #14264a;
    --card: #efefef;
    --backdrop: #262626;
    --white: #ffffff;
  }
  * { margin: 0; padding: 0; box-sizing: border-box; }
  html, body {
    width: 1200px;
    height: 576px;
    overflow: hidden;
    background: var(--backdrop);
    font-family: "Montserrat", sans-serif;
    color: var(--navy);
  }
  .stage { position: relative; width: 1200px; height: 576px; }

  .card {
    position: absolute;
    width: 484px;
    height: 292px;
    background: var(--card);
    border-radius: 8px;
    overflow: hidden;
  }
  .card--front { left: 102px; top: 139px; }
  .card--back  { left: 596px; top: 138px; width: 480px; }

  .wordmark { position: absolute; text-align: center; font-weight: 500; }
  .wordmark__name {
    display: block;
    letter-spacing: 0.42em;
    margin-right: -0.42em;
    line-height: 1;
  }
  .wordmark__sub {
    display: block;
    letter-spacing: 0.14em;
    margin-right: -0.14em;
    line-height: 1;
    font-weight: 400;
  }
  .card--front .wordmark { left: 0; width: 484px; top: 136px; }
  .card--front .wordmark__name { font-size: 37px; }
  .card--front .wordmark__sub { font-size: 15px; margin-top: 20px; }

  .card--back .wordmark { left: 256px; width: 200px; top: 66px; }
  .card--back .wordmark__name { font-size: 32px; }
  .card--back .wordmark__sub { font-size: 12px; margin-top: 17px; }

  .person { position: absolute; left: 26px; top: 50px; }
  .person__name { font-size: 22px; font-weight: 400; line-height: 1.1; }
  .person__title { font-size: 13.5px; font-weight: 400; margin-top: 2px; }

  .contact { position: absolute; left: 26px; top: 187px; list-style: none; }
  .contact__item {
    display: flex;
    align-items: center;
    height: 20px;
    font-size: 13px;
  }
  .contact__icon { width: 11px; height: 11px; margin-right: 9px; fill: var(--navy); }

  .band { position: absolute; left: 0; bottom: 0; width: 480px; height: 36px; }
  .band__shape { fill: var(--navy); }
  .tagline {
    position: absolute;
    right: 24px;
    bottom: 10px;
    font-size: 13px;
    color: var(--white);
    letter-spacing: 0.03em;
  }
</style>
</head>
<body>
<main class="stage">
  <section class="card card--front">
    <div class="wordmark">
      <span class="wordmark__name">ARVALE</span>
      <span class="wordmark__sub">WEALTH PARTNERS</span>
    </div>
  </section>

  <section class="card card--back">
    <div class="person">
      <p class="person__name">Daniel Morrow</p>
      <p class="person__title">Managing Director</p>
    </div>

    <div class="wordmark">
      <span class="wordmark__name">ARVALE</span>
      <span class="wordmark__sub">WEALTH PARTNERS</span>
    </div>

    <ul class="contact">
      <li class="contact__item">
        <svg class="contact__icon" viewBox="0 0 12 12" aria-hidden="true"><path d="M1 3.5C1 2 2.5 1 6 1s5 1 5 2.5V5H8.5V3.8h-5V5H1zM3 6h6l1.5 5h-9z"/></svg>
        555-014-2286
      </li>
      <li class="contact__item">
        <svg class="contact__icon" viewBox="0 0 12 12" aria-hidden="true"><path d="M0.5 2.5h11v7h-11z M1.5 3.3 6 6.6 10.5 3.3" stroke="#efefef" stroke-width="0.9"/></svg>
        daniel@arvalewealth.com
      </li>
      <li class="contact__item">
        <svg class="contact__icon" viewBox="0 0 12 12" aria-hidden="true"><circle cx="6" cy="6" r="5"/><path d="M1 6h10M6 1v10M6 1c-2.5 2.5-2.5 7.5 0 10M6 1c2.5 2.5 2.5 7.5 0 10" stroke="#efefef" stroke-width="0.8" fill="none"/></svg>
        www.arvalewealth.com
      </li>
    </ul>

    <svg class="band" viewBox="0 0 480 36" aria-hidden="true">
      <polygon class="band__shape" points="0,25 198,25 192,36 0,36"/>
      <path class="band__shape" d="M214,4 Q216,0 221,0 H480 V36 H200 Z"/>
    </svg>
    <p class="tagline">The Path from Saver to Steward</p>
  </section>
</main>
</body>
</html>
```